Sci Fi/ Secret Agent Author needs website design!

My name is Lark Whitby and I am an author. I require a site that can provide information about myself and my books and other works.

I would like it to have a Home, blog function, (about the) books/series section so people can visit another section and read about each individual book that's going to be released. A resources page, a Store, social media links and ability to load/embed videos from clipvane and other.

I write mild scifi/thriller/conspiracy/secret government type novels. -At the moment-. The series follows a strong female lead that is an agent with a secret organisation in a classified military installation.

The theme would be professional yet possibly show this element.

/military fiction/thriller/fantasy/Sci fi/ femme-fatal, readers. Mostly females, age 18-60
Novel readers

5+ page

• Would like designers to follow brief. :)
• My budget includes all the pages I will need;
• eg home, blog, resources, store, ability to pay with coinpouch and Credit Cards
• , ability to have trailers from clipvane etc. Must have links to the social media mentioned in the brief.
• use of the colours I have suggested. electric/indigo purple, fuschia highlights , dark greys
• as I will possibly base branding for social media ETC on the look of your website design and colour scheme.
• Ability for trailer on front page??
• Should not be too cluttered. (But I am open to all ideas)

```html
<!DOCTYPE html>
<html lang="en">
<head>
<meta charset="utf-8">
<title>Lark Whitby – Resources</title>
<link href="https://fonts.googleapis.com/css2?family=Roboto:wght@400;700&family=Roboto+Condensed:wght@400;700&family=Open+Sans:wght@400&display=swap" rel="stylesheet">
<style>
:root{
  --violet:#6a0aa8;
  --violet-bright:#7c1fd0;
  --ink:#333;
  --grey-text:#555;
  --dark:#2a2a2a;
  --footer-bg:#f3f3f3;
  --accent:#d0191f;
  --white:#fff;
}
*{margin:0;padding:0;box-sizing:border-box}
html,body{width:740px;height:1200px;overflow:hidden;background:var(--white)}
body{position:relative;font-family:'Open Sans',sans-serif;color:var(--ink)}
.abs{position:absolute}

.site-header{left:0;top:0;width:740px;height:59px;background:var(--violet)}
.brand{left:59px;top:14px;font:700 26px/1 'Roboto',sans-serif;color:var(--white);letter-spacing:.3px}
.main-nav{left:254px;top:25px;display:flex;gap:19px;font:400 9.5px/1 'Roboto Condensed',sans-serif;color:var(--white)}
.header-social{left:628px;top:25px;display:flex;gap:4px}
.header-social span{width:8px;height:8px;border-radius:50%;background:var(--white)}

.hero{left:0;top:59px;width:740px;height:232px;background:radial-gradient(ellipse at 60% 60%,#6b5a4c 0%,#3c2f2b 55%,#241c1c 100%)}
.hero-title{left:0;top:137px;width:740px;text-align:center;font:400 26px/1 'Roboto Condensed',sans-serif;color:var(--white)}
.hero-sub{left:0;top:170px;width:740px;text-align:center;font:400 9.5px/16px 'Roboto Condensed',sans-serif;color:var(--white)}
.hero-curve{left:0;top:250px}

.intro{left:120px;top:340px;width:500px;text-align:center;font:400 9.5px/16px 'Roboto',sans-serif;color:var(--grey-text)}

.photo-frame{left:60px;top:404px;width:246px;height:208px;border:1px solid #ddd;padding:3px;background:var(--white)}
.photo-frame div{width:100%;height:100%;background:linear-gradient(135deg,#5a4f46 0%,#8a7a6a 45%,#3a322c 100%)}
.body-copy{left:323px;top:411px;width:350px;font:400 6.7px/12.8px 'Open Sans',sans-serif;color:var(--grey-text)}
.body-copy p{margin-bottom:10px}

.newsletter{left:0;top:677px;width:740px;height:307px;background:linear-gradient(180deg,#6a2fd8 0%,#8a3fd0 60%,#7a34c4 100%)}
.video-frame{left:88px;top:741px;width:285px;height:184px;border:3px solid #ddd;background:linear-gradient(135deg,#3b4a66 0%,#6d8299 50%,#1f2636 100%)}
.play{left:125px;top:72px;width:30px;height:30px;border:2px solid var(--white);border-radius:50%}
.play:after{content:"";position:absolute;left:10px;top:7px;border-left:10px solid var(--white);border-top:6px solid transparent;border-bottom:6px solid transparent}
.progress{left:18px;top:158px;width:187px;height:4px;background:#777}
.progress span{display:block;width:55%;height:100%;background:var(--accent)}
.news-title{left:407px;top:752px;font:700 20px/1 'Roboto Condensed',sans-serif;color:var(--white)}
.news-text{left:407px;top:779px;width:245px;font:400 6.5px/11.5px 'Open Sans',sans-serif;color:var(--white)}
.field{left:408px;width:240px;height:26px;background:var(--white);border:1px solid #ccc;font:400 7px/26px 'Open Sans',sans-serif;color:#555;text-align:center}
.subscribe{left:408px;top:888px;width:240px;height:26px;background:var(--dark);color:var(--white);font:400 11px/26px 'Roboto Condensed',sans-serif;text-align:center}

.site-footer{left:0;top:984px;width:740px;height:178px;background:var(--footer-bg)}
.footer-brand{left:60px;top:1018px;font:700 25px/1 'Roboto Condensed',sans-serif;color:var(--violet-bright)}
.footer-about{left:60px;top:1052px;width:182px;font:400 7px/12.8px 'Open Sans',sans-serif;color:var(--grey-text)}
.footer-head{top:1016px;font:400 12px/1 'Roboto Condensed',sans-serif;color:var(--ink)}
.contact-list{left:292px;top:1042px;font:400 7.5px/12.8px 'Open Sans',sans-serif;color:var(--grey-text)}
.contact-list li{list-style:none;position:relative;padding-left:17px;margin-bottom:7px}
.contact-list li.phone{font-size:8.5px}
.contact-list svg{position:absolute;left:0;top:2px}
.quick-links{left:488px;top:1040px;font:400 6.5px/12.7px 'Open Sans',sans-serif;color:var(--grey-text)}
.quick-links li{list-style:none;padding-left:10px;position:relative}
.quick-links li:before{content:"";position:absolute;left:0;top:4px;border-left:3px solid #444;border-top:2.5px solid transparent;border-bottom:2.5px solid transparent}
.social-list{left:615px;top:1041px;font:400 8.5px/1 'Open Sans',sans-serif;color:var(--grey-text)}
.social-list li{list-style:none;display:flex;align-items:center;gap:6px;height:21px}
.social-list li span{width:15px;height:15px;border:1px solid #555;border-radius:50%}
.legal{left:0;top:1162px;width:740px;border-top:1px solid #ddd;padding-top:14px;text-align:center;font:400 6.5px/1 'Open Sans',sans-serif;color:var(--grey-text)}
</style>
</head>
<body>

<header class="site-header abs">
  <div class="brand abs">LARK WHITBY</div>
  <nav class="main-nav abs"><span>HOME</span><span>BOOKS</span><span>BLOG</span><span>RESOURCES</span><span>OTHER WORKS</span><span>STORE</span><span>CONTACT US</span></nav>
  <div class="header-social abs"><span></span><span></span><span></span><span></span><span></span></div>
</header>

<section class="hero abs" role="img" aria-label="Close-up of hands holding an open book in dim light"></section>
<h1 class="hero-title abs">RESOURCES</h1>
<p class="hero-sub abs">SED UT PERSPICIATIS UNDE OMNIS ISTE NATUS ERROR SIT VOLUPTATEM<br>ACCUSANTIUM DOLOREMQUE LAUDANTIUM, TOTAM REM</p>
<svg class="hero-curve abs" width="740" height="45" viewBox="0 0 740 45">
  <path d="M0 9 Q370 60 740 12 L740 45 L0 45 Z" fill="#fff"/>
  <path d="M0 9 Q370 60 740 12" fill="none" stroke="#7c1fd0" stroke-width="3"/>
</svg>

<p class="intro abs">Sed ut perspiciatis unde omnis iste natus error sit voluptatem accusantium doloremque laudantium, totam rem aperiam, eaque ipsa quae ab illo inventore veritatis et quasi architecto beatae vitae dicta sunt explicabo.</p>

<div class="photo-frame abs"><div role="img" aria-label="Child lying on a rug reading a book in a cosy room"></div></div>
<div class="body-copy abs">
  <p>Sed ut perspiciatis unde omnis iste natus error sit voluptatem accusantium doloremque laudantium, totam rem aperiam, eaque ipsa quae ab illo inventore veritatis et quasi architecto beatae vitae dicta sunt explicabo. Nemo enim ipsam voluptatem quia voluptas sit aspernatur aut odit aut fugit, sed quia consequuntur magni dolores eos qui ratione voluptatem sequi nesciunt. Neque porro quisquam est, qui dolorem ipsum quia dolor sit amet, consectetur, adipisci velit, sed quia non numquam</p>
  <p>Lorem ipsum dolor sit amet, consectetur adipiscing elit, sed do eiusmod tempor incididunt ut labore et dolore magna aliqua. Ut enim ad minim veniam, quis nostrud exercitation ullamco laboris nisi ut aliquip ex ea commodo consequat. Duis aute irure dolor in reprehenderit in voluptate velit esse cillum dolore eu fugiat nulla pariatur. Excepteur sint occaecat cupidatat non proident, sunt in culpa qui officia deserunt mollit anim id est laborum</p>
  <p>Nemo enim ipsam voluptatem quia voluptas sit aspernatur aut odit aut fugit, sed quia consequuntur magni dolores eos qui ratione voluptatem sequi nesciunt. Neque porro quisquam est, qui dolorem ipsum quia dolor sit amet, consectetur, adipisci velit, sed quia non numquam eius modi tempora</p>
</div>

<section class="newsletter abs" role="img" aria-label="Purple-tinted desert road between hills"></section>
<div class="video-frame abs" role="img" aria-label="Video trailer still of a reader with a glowing book in a library">
  <div class="play abs"></div>
  <div class="progress abs"><span></span></div>
</div>
<h2 class="news-title abs">SIGN UP FOR OUR NEWSLETTER</h2>
<p class="news-text abs">Sed ut perspiciatis unde omnis iste natus error sit voluptatem accusantium doloremque laudantium, totam rem aperiam, eaque ipsa quae ab illo inventore veritatis et quasi architecto beatae vitae dicta sunt explicabo</p>
<div class="field abs" style="top:825px">Enter Name</div>
<div class="field abs" style="top:857px">Enter Email</div>
<div class="subscribe abs">SUBSCRIBE</div>

<footer class="site-footer abs"></footer>
<div class="footer-brand abs">LARK WHITBY</div>
<p class="footer-about abs">Sed ut perspiciatis unde omnis iste natus error sit voluptatem accusantium doloremque lauantium, totam rem aperiam, eaque ipsa quae ab illo inventore veritatis et quasi architecto beatae vitae dicta sunt explicabo</p>

<h3 class="footer-head abs" style="left:292px">CONTACT US</h3>
<ul class="contact-list abs">
  <li><svg width="9" height="10" viewBox="0 0 9 10"><path d="M4.5 9.5 C1 5.5 1 4.5 1 3.8 A3.5 3.5 0 0 1 8 3.8 C8 4.5 8 5.5 4.5 9.5Z" fill="none" stroke="#444"/><circle cx="4.5" cy="3.8" r="1.2" fill="#444"/></svg>Lark Whitby<br>Harrow Lane 14 20817 Northgate</li>
  <li class="phone"><svg width="9" height="9" viewBox="0 0 9 9"><path d="M1 1.5 L3 1 L4 3 L3 4 Q4 5.5 5 6 L6 5 L8 6 L7.5 8 Q3 8 1 1.5Z" fill="#444"/></svg>Phone: +44 555 01 23 456</li>
  <li><svg width="9" height="7" viewBox="0 0 9 7"><rect x="0.5" y="0.5" width="8" height="6" fill="#444"/><path d="M0.5 0.5 L4.5 4 L8.5 0.5" fill="none" stroke="#f3f3f3"/></svg>hello@larkwhitby.example</li>
</ul>

<h3 class="footer-head abs" style="left:486px">QUICK LINKS</h3>
<ul class="quick-links abs"><li>Home</li><li>About the book</li><li>Blog</li><li>Resources</li><li>Blog</li><li>store</li><li>Contact Us</li></ul>

<h3 class="footer-head abs" style="left:616px">SOCIAL</h3>
<ul class="social-list abs">
  <li><span></span>Friendwall</li><li><span></span>Chirper</li><li><span></span>Snapframe</li><li><span></span>Pinboardly</li><li><span></span>clipvane</li>
</ul>

<div class="legal abs">©2017 Lark Whitby, All Rights Reserved.</div>
</body>
</html>
```